Yacht, Boats, Watersports company needs a redesign of business card

Hello Designers!
We are a Boat dealership company that sells fun in the water, we sell boats, Yachts, Kayaks and also yacht WaterSport toys. We are looking to redesign our business cards in to something a little bit more sophisticated. in a way that we can make better use of our company colors. I'm attaching a zipped file containing the company 3 sets of company logo which one is an horizontal another one is a vertical and also a chromed 3d logo. Also is included two set of business cards that we use and also some designs that i think it's interesting. We use PMS 2026c Orange and PMS 7687C Blue. I would like to see at least two different options with the orange as accent and also using blue as an accent color. It's really important for the business cards to have a font option and size that is legible to most people. Our current website is wwww.coralpennant.com. Please visit if you want to have a better feeling of the Boat dealership
You can send Single sided or double side options. We are now using single sided but we may be open for a double side option if we really like the design.
Target Market(s)
Marine, boat sales, yacht sales, water toys sales/
Contact Information for Business Card
Name: Dale Whitcombe
Address: 212 North Fenwick Lane,
Marlow Key, FL 33412
Phone: 954-731-8842
Fax: 954:731-8843
Cell: 954-382-1490
Email: dw@coralpennant.com
Website: coralpennant.com
Requirements
Must have
- the current information of the business card provided.
logo
use the PMS Colors
Nice to have
- a touch of elegance and sophistication but simple
Should not have
- should not have any typography that is hard to read, the card should be simple but yet sophisticated.

```html
<!DOCTYPE html>
<html lang="en">
<head>
<meta charset="utf-8">
<title>Coral Pennant – Business Card</title>
<link rel="stylesheet" href="https://fonts.googleapis.com/css2?family=Montserrat:wght@700&family=Roboto+Condensed:wght@400;700&family=Roboto:wght@400&display=swap">
<style>
  :root {
    --brand-blue: #1a5aa6;
    --brand-orange: #f07124;
    --bleed-grey: #a7a7a7;
    --card-white: #ffffff;
    --label-ink: #333333;
  }
  * { margin: 0; padding: 0; box-sizing: border-box; }
  html, body {
    width: 1200px; height: 1200px; overflow: hidden;
    background: #ffffff;
  }
  .sheet { position: relative; width: 1200px; height: 1200px; }

  .bleed-area {
    position: absolute;
    background: var(--bleed-grey);
  }
  .bleed-area--front { left: 150px; top: 156px; width: 561px; height: 338px; }
  .bleed-area--back  { left: 552px; top: 767px; width: 563px; height: 335px; }

  .bleed-label {
    position: absolute;
    font-family: "Roboto", Arial, sans-serif;
    font-size: 12px;
    color: var(--label-ink);
    line-height: 1;
  }
  .bleed-label--side { transform: rotate(90deg); transform-origin: left top; }

  .card {
    position: absolute;
    background: var(--card-white);
    border-radius: 22px;
    overflow: hidden;
  }
  .card--front { left: 167px; top: 173px; width: 527px; height: 304px; }
  .card--back  { left: 571px; top: 785px; width: 527px; height: 298px; }

  .band { position: absolute; left: 0; width: 100%; }
  .band--blue { top: 0; background: var(--brand-blue); }
  .band--orange { bottom: 0; background: var(--brand-orange); }
  .card--front .band--blue { height: 50px; }
  .card--front .band--orange { height: 48px; }
  .card--back .band--blue { height: 48px; }
  .card--back .band--orange { height: 46px; }

  /* Front */
  .brand-mark {
    position: absolute; left: 218px; top: 80px;
    width: 92px; height: 92px;
    border: 7px solid var(--brand-orange);
    border-radius: 50%;
  }
  .brand-name {
    position: absolute; left: 0; top: 195px; width: 100%;
    text-align: center;
    font-family: "Montserrat", Arial, sans-serif;
    font-weight: 700;
    font-size: 30px;
    letter-spacing: 0.5px;
    color: var(--brand-blue);
  }
  .web-address {
    position: absolute; left: 0; bottom: 18px; width: 100%;
    text-align: center;
    font-family: "Roboto", Arial, sans-serif;
    font-size: 14px;
    letter-spacing: 3px;
    color: var(--card-white);
  }

  /* Back */
  .person { position: absolute; left: 21px; top: 76px; }
  .person-name {
    font-family: "Roboto Condensed", Arial Narrow, sans-serif;
    font-weight: 700; font-size: 20px;
    color: var(--brand-orange); line-height: 1;
  }
  .person-title {
    margin-top: 4px;
    font-family: "Roboto Condensed", Arial Narrow, sans-serif;
    font-weight: 700; font-size: 12px;
    color: var(--brand-blue); letter-spacing: 0.3px;
  }
  .social-row {
    position: absolute; left: 21px; top: 193px;
    display: flex; gap: 10px;
  }
  .social-slot {
    width: 24px; height: 24px;
    background: var(--brand-blue); border-radius: 3px;
  }

  .contact-list {
    position: absolute; left: 233px; top: 70px;
    list-style: none;
    font-family: "Roboto Condensed", Arial Narrow, sans-serif;
    font-size: 14px; line-height: 17px;
    color: var(--brand-blue);
  }
  .contact-item {
    display: flex; align-items: center; gap: 10px;
    margin-bottom: 9px;
  }
  .contact-icon { flex: 0 0 24px; width: 24px; height: 24px; }
</style>
</head>
<body>
<div class="sheet">

  <!-- Front side -->
  <div class="bleed-area bleed-area--front"></div>
  <span class="bleed-label bleed-label--side" style="left:166px; top:290px;">bleed</span>
  <span class="bleed-label" style="left:350px; top:480px;">bleed</span>

  <section class="card card--front">
    <div class="band band--blue"></div>
    <div class="brand-mark" aria-hidden="true"></div>
    <div class="brand-name">CORAL PENNANT</div>
    <div class="band band--orange"></div>
    <div class="web-address">www.coralpennant.com</div>
  </section>

  <!-- Back side -->
  <div class="bleed-area bleed-area--back"></div>
  <span class="bleed-label bleed-label--side" style="left:568px; top:955px;">bleed</span>
  <span class="bleed-label" style="left:748px; top:1088px;">bleed</span>

  <section class="card card--back">
    <div class="band band--blue"></div>

    <div class="person">
      <div class="person-name">DALE WHITCOMBE</div>
      <div class="person-title">CORPORATE MANAGER</div>
    </div>

    <div class="social-row" aria-label="Social links">
      <span class="social-slot"></span>
      <span class="social-slot"></span>
      <span class="social-slot"></span>
    </div>

    <ul class="contact-list">
      <li class="contact-item">
        <svg class="contact-icon" viewBox="0 0 24 24" aria-label="Phone">
          <circle cx="12" cy="12" r="12" fill="var(--brand-orange)"/>
          <rect x="6" y="9" width="12" height="8" rx="1.5" fill="#fff"/>
          <rect x="8" y="6" width="8" height="4" rx="1" fill="#fff"/>
        </svg>
        <span>1.954.731.8842<br>1.954.382.1490</span>
      </li>
      <li class="contact-item">
        <svg class="contact-icon" viewBox="0 0 24 24" aria-label="Fax">
          <circle cx="12" cy="12" r="12" fill="var(--brand-orange)"/>
          <rect x="6" y="10" width="12" height="7" rx="1.5" fill="#fff"/>
          <rect x="8.5" y="6" width="7" height="5" fill="#fff"/>
        </svg>
        <span>1.954.731.8843</span>
      </li>
      <li class="contact-item">
        <svg class="contact-icon" viewBox="0 0 24 24" aria-label="Address">
          <circle cx="12" cy="12" r="12" fill="var(--brand-orange)"/>
          <path d="M5 12 L12 6 L19 12 L17 12 L17 18 L7 18 L7 12 Z" fill="#fff"/>
          <rect x="10.5" y="14" width="3" height="4" fill="var(--brand-orange)"/>
        </svg>
        <span>212 North Fenwick Lane<br>Marlow Key, FL 33412</span>
      </li>
      <li class="contact-item">
        <svg class="contact-icon" viewBox="0 0 24 24" aria-label="Email">
          <circle cx="12" cy="12" r="12" fill="var(--brand-orange)"/>
          <rect x="6" y="8" width="12" height="9" rx="1" fill="#fff"/>
          <path d="M6.5 8.5 L12 13 L17.5 8.5" fill="none" stroke="var(--brand-orange)" stroke-width="1.2"/>
        </svg>
        <span>dw@coralpennant.com</span>
      </li>
    </ul>

    <div class="band band--orange"></div>
  </section>

</div>
</body>
</html>
```